Gaming Headset Packaging Design

We would like a gaming window box style packaging design for our gaming headset.

We want to use the packaging for 2-3 of our gaming headphone series and hence we would not like to put any product pictures on the packaging.

Size: (enclosed die-cut drawing) please feel free to modify the shape of the window
Material: E Flute Paper box
Type: Window Box style
Design features we prefer: gaming, playful, creative, trendy, High tech.
Requirement: AI file is preferred

Enclosed are a detailed description along with competitor designs and existing die-cut drawing (AI format) for your reference.

Any further questions, please feel free to ask.

```html
<!DOCTYPE html>
<html lang="en">
<head>
<meta charset="utf-8">
<title>Pro Gaming Headset 7.1 – Window Box Packaging</title>
<link rel="stylesheet" href="https://fonts.googleapis.com/css2?family=Exo+2:ital,wght@1,800&family=Arimo:wght@400&display=swap">
<style>
  :root {
    --board: #3a3a3c;
    --board-side: #313133;
    --paper: #ffffff;
    --backdrop: #ffffff;
    --window-light: #eef1f4;
    --window-shade: #c9d1da;
    --product-blue: #1d5f9a;
    --accent-blue: #12a6e4;
    --accent-red: #e8292f;
    --accent-yellow: #fff200;
  }
  html, body {
    margin: 0;
    padding: 0;
    width: 1200px;
    height: 575px;
    overflow: hidden;
    background: var(--backdrop);
  }
  .packaging-range {
    display: block;
    width: 1200px;
    height: 575px;
  }
  .panel-front, .panel-side { fill: var(--board); }
  .panel-side { fill: var(--board-side); }
  .title-main {
    font-family: "Exo 2", sans-serif;
    font-style: italic;
    font-weight: 800;
    fill: var(--paper);
  }
  .title-sub {
    font-family: "Exo 2", sans-serif;
    font-style: italic;
    font-weight: 800;
  }
  .feature-list {
    font-family: "Arimo", sans-serif;
    font-size: 9.5px;
    fill: var(--paper);
  }
  .window-view { fill: url(#windowGlow); }
  .window-frame { fill: none; stroke-width: 5; stroke-linejoin: miter; }
  .series-blue   { --accent: var(--accent-blue); }
  .series-red    { --accent: var(--accent-red); }
  .series-yellow { --accent: var(--accent-yellow); }
  .accent-fill   { fill: var(--accent); }
  .accent-stroke { stroke: var(--accent); }
  .sub-red { fill: var(--accent-red); }
</style>
</head>
<body>
<svg class="packaging-range" viewBox="0 0 1200 575" xmlns="http://www.w3.org/2000/svg">
  <defs>
    <linearGradient id="windowGlow" x1="0" y1="0" x2="1" y2="1">
      <stop offset="0" stop-color="var(--window-light)"/>
      <stop offset="0.6" stop-color="var(--window-shade)"/>
      <stop offset="1" stop-color="var(--product-blue)"/>
    </linearGradient>

    <g id="featureText">
      <text class="feature-list" x="28" y="192">Features:</text>
      <text class="feature-list" x="36" y="204">Virtual 7.1 Surround Sound</text>
      <text class="feature-list" x="28" y="216">Dual Drivers on each ear for Accuracy</text>
      <text class="feature-list" x="28" y="228">3D Sound Vibration</text>
      <text class="feature-list" x="28" y="240">Bendable Stainless-Steel headband</text>
      <text class="feature-list" x="28" y="252">Soft and soothing earpads</text>
    </g>
  </defs>

  <!-- Blue series -->
  <g class="package series-blue" transform="translate(40,145)">
    <rect class="panel-side" x="0" y="0" width="60" height="290"/>
    <g transform="translate(22,20) rotate(90)">
      <text class="title-main" x="0" y="0" font-size="26">Pro Gaming</text>
      <text class="title-sub accent-fill" x="0" y="16" font-size="15">Headset 7.1</text>
    </g>
    <g transform="translate(60,0)">
      <rect class="panel-front" width="300" height="290"/>
      <text class="title-main" x="40" y="68" font-size="28">Pro Gaming</text>
      <text class="title-sub accent-fill" x="44" y="88" font-size="17">Headset 7.1</text>
      <polygon class="window-view" role="img" aria-label="Headset seen through the window"
        points="300,42 238,42 222,58 222,110 232,122 232,202 218,218 300,218"/>
      <polyline class="window-frame accent-stroke"
        points="300,42 238,42 222,58 222,110 232,122 232,202 218,218 300,218"/>
      <use href="#featureText"/>
      <polygon class="band accent-fill" points="20,290 20,264 168,258 186,290"/>
    </g>
  </g>

  <!-- Red series -->
  <g class="package series-red" transform="translate(420,145)">
    <rect class="panel-side" x="0" y="0" width="60" height="290"/>
    <g transform="translate(22,20) rotate(90)">
      <text class="title-main" x="0" y="0" font-size="26">Pro Gaming</text>
      <text class="title-sub accent-fill" x="0" y="16" font-size="15">Headset 7.1</text>
    </g>
    <g transform="translate(60,0)">
      <rect class="panel-front" width="300" height="290"/>
      <text class="title-main" x="40" y="68" font-size="28">Pro Gaming</text>
      <text class="title-sub accent-fill" x="44" y="88" font-size="17">Headset 7.1</text>
      <polygon class="window-view" role="img" aria-label="Headset seen through the window"
        points="300,42 238,42 222,58 222,110 232,122 232,202 218,218 300,218"/>
      <polyline class="window-frame accent-stroke"
        points="300,42 238,42 222,58 222,110 232,122 232,202 218,218 300,218"/>
      <use href="#featureText"/>
      <polygon class="band accent-fill" points="20,290 20,264 168,258 186,290"/>
    </g>
  </g>

  <!-- Yellow series -->
  <g class="package series-yellow" transform="translate(800,145)">
    <rect class="panel-side" x="0" y="0" width="60" height="290"/>
    <g transform="translate(22,20) rotate(90)">
      <text class="title-main" x="0" y="0" font-size="26">Pro Gaming</text>
      <text class="title-sub accent-fill" x="0" y="16" font-size="15">Headset 7.1</text>
    </g>
    <g transform="translate(60,0)">
      <rect class="panel-front" width="300" height="290"/>
      <text class="title-main" x="40" y="68" font-size="28">Pro Gaming</text>
      <text class="title-sub sub-red" x="44" y="88" font-size="17">Headset 7.1</text>
      <polygon class="window-view" role="img" aria-label="Headset seen through the window"
        points="300,42 238,42 222,58 222,110 232,122 232,202 218,218 300,218"/>
      <polyline class="window-frame accent-stroke"
        points="300,42 238,42 222,58 222,110 232,122 232,202 218,218 300,218"/>
      <use href="#featureText"/>
      <polygon class="band accent-fill" points="20,290 20,264 168,258 186,290"/>
    </g>
  </g>
</svg>
</body>
</html>
```